Info graphics

We have four infographics that we want recreated. We want the same information displayed but original artwork

Requirements
Must have
• We require a re-creation of each of the 4 infographics attached.

```html
<!DOCTYPE html>
<html lang="en">
<head>
<meta charset="UTF-8">
<title>The Landscape of 5G</title>
<link href="https://fonts.googleapis.com/css2?family=Roboto:wght@300;400;700;900&family=Roboto+Condensed:wght@700&display=swap" rel="stylesheet">
<style>
  :root {
    --accent: #e8a834;
    --ink: #111111;
    --text: #2a2a2a;
    --paper: #ffffff;
  }
  * { margin: 0; padding: 0; box-sizing: border-box; }
  html, body { width: 1200px; height: 675px; overflow: hidden; background: var(--paper); }
  .canvas { position: relative; width: 1200px; height: 675px; font-family: "Roboto", Arial, sans-serif; color: var(--text); }
  .title {
    position: absolute; top: 44px; left: 0; width: 100%; text-align: center;
    font-family: "Roboto Condensed", "Roboto", sans-serif; font-weight: 700;
    font-size: 52px; line-height: 1; color: var(--ink); letter-spacing: 0.2px;
  }
  .title-rule { position: absolute; top: 112px; left: 506px; width: 171px; height: 4px; border-radius: 2px; background: var(--accent); }
  .subtitle {
    position: absolute; top: 128px; left: 0; width: 100%; text-align: center;
    font-weight: 300; font-size: 32px; line-height: 1.2; color: var(--ink);
  }
  .stat { position: absolute; width: 340px; }
  .stat-head { display: flex; align-items: center; height: 91px; }
  .stat-icon { width: 91px; height: 91px; flex: none; }
  .stat-value {
    margin-left: 9px; font-weight: 900; font-size: 92px; line-height: 1;
    color: var(--accent); letter-spacing: -1px; transform: translateY(2px);
  }
  .stat-label {
    margin-top: 18px; font-family: "Roboto Condensed", "Roboto", sans-serif;
    font-weight: 700; font-size: 21px; color: var(--ink); line-height: 1.2;
  }
  .stat-text { margin-top: 5px; font-weight: 300; font-size: 18px; line-height: 22px; color: var(--ink); }
  .stat--latency { left: 99px; top: 208px; }
  .stat--density { left: 441px; top: 208px; }
  .stat--throughput { left: 783px; top: 208px; }
  .stat--throughput .stat-label { margin-top: 22px; }
  .stat--throughput .stat-text { margin-top: 1px; }
  .stat--spectrum { left: 99px; top: 423px; }
  .stat--traffic { left: 441px; top: 423px; }
  .stat--network { left: 783px; top: 423px; }
  .stat--spectrum .stat-label, .stat--traffic .stat-label, .stat--network .stat-label { margin-top: 20px; }
  .icon-line { fill: none; stroke: var(--paper); stroke-width: 3; stroke-linecap: round; stroke-linejoin: round; }
  .icon-fill { fill: var(--paper); }
</style>
</head>
<body>
<div class="canvas">
  <h1 class="title">The Landscape of 5G</h1>
  <div class="title-rule"></div>
  <p class="subtitle">5G will differenciate itself by delivering various improvements:</p>

  <section class="stat stat--latency">
    <div class="stat-head">
      <svg class="stat-icon" viewBox="0 0 91 91" aria-hidden="true">
        <circle cx="45.5" cy="45.5" r="45.5" fill="var(--accent)"/>
        <circle class="icon-line" cx="45" cy="50" r="24"/>
        <circle class="icon-line" cx="45" cy="50" r="18" stroke-width="2"/>
        <rect class="icon-line" x="39" y="19" width="12" height="6" stroke-width="2.5"/>
        <line class="icon-line" x1="45" y1="25" x2="45" y2="26"/>
        <line class="icon-line" x1="63" y1="29" x2="68" y2="24"/>
        <line class="icon-line" x1="45" y1="50" x2="53" y2="42"/>
        <circle class="icon-fill" cx="45" cy="50" r="3"/>
      </svg>
      <div class="stat-value">10x</div>
    </div>
    <h2 class="stat-label">Decrease in latency</h2>
    <p class="stat-text">Delivering latency as low as 1ms.</p>
  </section>

  <section class="stat stat--density">
    <div class="stat-head">
      <svg class="stat-icon" viewBox="0 0 91 91" aria-hidden="true">
        <circle cx="45.5" cy="45.5" r="45.5" fill="var(--accent)"/>
        <path class="icon-line" stroke-width="6" d="M20 40 Q45.5 18 71 40"/>
        <path class="icon-line" stroke-width="6" d="M29 49 Q45.5 35 62 49"/>
        <path class="icon-line" stroke-width="6" d="M38 58 Q45.5 52 53 58"/>
        <circle class="icon-fill" cx="45.5" cy="67" r="4.5"/>
      </svg>
      <div class="stat-value">10x</div>
    </div>
    <h2 class="stat-label">Connection Density</h2>
    <p class="stat-text">Delivering latency as low as 1ms.</p>
  </section>

  <section class="stat stat--throughput">
    <div class="stat-head">
      <svg class="stat-icon" viewBox="0 0 91 91" aria-hidden="true">
        <circle cx="45.5" cy="45.5" r="45.5" fill="var(--accent)"/>
        <path class="icon-line" d="M24 64 A26 26 0 1 1 67 64"/>
        <path class="icon-line" stroke-width="2" d="M30 58 A19 19 0 1 1 61 58"/>
        <line class="icon-line" x1="45.5" y1="50" x2="63" y2="56"/>
        <circle class="icon-line" cx="45.5" cy="50" r="4" stroke-width="2.5"/>
        <line class="icon-line" x1="38" y1="64" x2="53" y2="64" stroke-width="2.5"/>
        <line class="icon-line" x1="41" y1="69" x2="50" y2="69" stroke-width="2.5"/>
      </svg>
      <div class="stat-value">10x</div>
    </div>
    <h2 class="stat-label">Experienced Throughput</h2>
    <p class="stat-text">Bringing more uniform,<br>multi-Gbps peak rates</p>
  </section>

  <section class="stat stat--spectrum">
    <div class="stat-head">
      <svg class="stat-icon" viewBox="0 0 91 91" aria-hidden="true">
        <circle cx="45.5" cy="45.5" r="45.5" fill="var(--accent)"/>
        <circle class="icon-fill" cx="45" cy="42" r="3"/>
        <path class="icon-line" stroke-width="2.5" d="M38 47 A9 9 0 1 1 52 47"/>
        <path class="icon-line" stroke-width="2.5" d="M33 51 A15 15 0 1 1 57 51"/>
        <path class="icon-line" stroke-width="2.5" d="M45 45 L34 78 M45 45 L56 78 M38 66 L52 66 M36 72 L54 72 M28 78 L62 78"/>
        <path class="icon-fill" d="M58 14 L52 26 L57 26 L54 34 L62 22 L57 22 Z"/>
      </svg>
      <div class="stat-value">3x</div>
    </div>
    <h2 class="stat-label">Spectrum Efficiency:</h2>
    <p class="stat-text">Achieving even more bits pe Hz with<br>advanced antenna techniques.</p>
  </section>

  <section class="stat stat--traffic">
    <div class="stat-head">
      <svg class="stat-icon" viewBox="0 0 91 91" aria-hidden="true">
        <defs>
          <g id="mini-tower">
            <circle cx="0" cy="0" r="3" fill="none" stroke="#fff" stroke-width="1.3"/>
            <circle cx="0" cy="0" r="1" fill="#fff"/>
            <path d="M0 2 L-4 10 M0 2 L4 10 M-5 10 L5 10" fill="none" stroke="#fff" stroke-width="1.3" stroke-linecap="round"/>
          </g>
        </defs>
        <circle cx="45.5" cy="45.5" r="45.5" fill="var(--accent)"/>
        <use href="#mini-tower" x="28" y="24"/><use href="#mini-tower" x="45.5" y="24"/><use href="#mini-tower" x="63" y="24"/>
        <use href="#mini-tower" x="28" y="42"/><use href="#mini-tower" x="45.5" y="42"/><use href="#mini-tower" x="63" y="42"/>
        <use href="#mini-tower" x="28" y="60"/><use href="#mini-tower" x="45.5" y="60"/><use href="#mini-tower" x="63" y="60"/>
      </svg>
      <div class="stat-value">100x</div>
    </div>
    <h2 class="stat-label">Traffic Capacity</h2>
    <p class="stat-text">Driving network hyper-densification<br>with more small cells everywhere</p>
  </section>

  <section class="stat stat--network">
    <div class="stat-head">
      <svg class="stat-icon" viewBox="0 0 91 91" aria-hidden="true">
        <circle cx="45.5" cy="45.5" r="45.5" fill="var(--accent)"/>
        <rect class="icon-line" x="36" y="22" width="19" height="13" stroke-width="2.2"/>
        <path class="icon-line" stroke-width="2.2" d="M45.5 35 V47 M33 47 H58 M33 47 V53 M58 47 V53"/>
        <rect class="icon-line" x="22" y="53" width="20" height="13" stroke-width="2.2"/>
        <rect class="icon-line" x="49" y="53" width="20" height="13" stroke-width="2.2"/>
        <path class="icon-line" stroke-width="2.2" d="M28 70 H36 M55 70 H63"/>
      </svg>
      <div class="stat-value">100x</div>
    </div>
    <h2 class="stat-label">Network Efficiency</h2>
    <p class="stat-text">Optimizing network energy consumption<br>with more efficient processing</p>
  </section>
</div>
</body>
</html>
```